Commercial/Corporate Law Firm needs Website Design

Hi guys. I've started up a new law firm and would love your help designing an attractive website. I'll need both design and coding, and to make it easy for us to edit as necessary later, I think it should be built off a Wordpress.org structure.
FIRST IMPRESSIONS
It's very important that the first impression of the website really captures our prospective clients' attention and impresses them. Their first three seconds needs to be good.
I imagine the homepage may be short, with a menu bar and a compelling image, and with a tagline overlaid or underneath (eg. "It's about results.")
The image should be related to our practice areas: eg. IPOs, corporate transactions, or commercial negotiations.
I have previously suggested there could be a skyline image of Sydney or Adelaide. However, because we are based in Adelaide, I don't think Sydney is appropriate - and Adelaide is probably too boring to use.
HOMEPAGE
Being a new firm, we don't have many existing testimonials, and I will be the only lawyer to start with. So we need to focus on the nature of the services we will provide and how my experience can help them. We have an existing logo to use, and I would like the website colour scheme not to clash with that logo (dark blue and white).
After the initial image and tagline there should be a brief introduction to each of the main areas of work, eg. "We specialise in three main areas of practice:"
1. Corporate Transactions and Regulation
2. Business Law and Dispute Resolution
3. Migration Assistance
These should each have an appropriate photo and link to a separate page that briefly describes our services in that area.
Below that there should be a message from me with a photo. Finally, at the bottom, there should be a "Contact Us" section which shows a Google image of our address, contact details, and then our logo with colours inverted.
OTHER PAGES
While we will need some other pages, they should all be fairly simple. I think we will need one page to say "About Us", where I will put information about my experience. I think we will then need one page for each of the 3 areas listed above, which just needs an appropriate image and then text to describe the service. Finally, a "Contact Us" page which I imagine will be the same as the bottom of the homepage.
OTHER DETAILS
For now you can use details from my LinkedIn page to fill out any other text as necessary, or the photo.
Because the logo is square, I would prefer the design of the website also to be rectangular.
Looking forward to seeing your work! Thank you.
Marcus
Potential clients:
Businesses with legal issues or disputes
Companies wishing to list on the stock market

```html
<!DOCTYPE html>
<html lang="en">
<head>
<meta charset="utf-8">
<title>Castellan Legal</title>
<link href="https://fonts.googleapis.com/css2?family=Montserrat:wght@500;600;700&family=Lora:wght@500;600;700&family=Open+Sans:wght@400;600&display=swap" rel="stylesheet">
<style>
:root{
  --navy:#0d2a5c;
  --brand:#0c3b8f;
  --brand-dark:#0a3380;
  --ink:#1d1d1d;
  --body:#3a3a3a;
  --paper:#ffffff;
  --mist:#f6f4f5;
  --rule:#e3e3e3;
}
*{box-sizing:border-box;margin:0;padding:0}
html,body{width:685px;height:1200px;overflow:hidden;background:var(--paper)}
body{position:relative;font-family:"Open Sans",Arial,sans-serif;color:var(--body)}
.abs{position:absolute}

/* hero */
.hero{left:0;top:0;width:685px;height:345px;
  background:linear-gradient(180deg,#2f3f86 0%,#5a5fa8 30%,#b59ab8 50%,#f0a86a 62%,#d9773b 70%,#1f2540 82%,#2b3b66 100%)}
.brand{display:flex;align-items:center;gap:7px;color:var(--paper);font-family:"Lora",Georgia,serif;font-weight:600;letter-spacing:1.5px}
.hero .brand{left:74px;top:38px;font-size:15px}
.brand-square{width:22px;height:22px;background:var(--navy);border:1px solid rgba(255,255,255,.6)}
.nav{right:66px;top:13px;display:flex;gap:6px;align-items:center}
.nav a{font-family:"Montserrat",Arial,sans-serif;font-weight:700;font-size:7.5px;color:var(--paper);text-decoration:none;padding:5px 7px}
.nav a.is-active{background:var(--brand)}
.nav a+a{margin-left:4px}
.tagline{left:255px;top:103px;width:176px;border-top:1.5px solid var(--paper);padding-top:5px;
  font-family:"Montserrat",Arial,sans-serif;font-weight:700;font-size:19px;color:var(--paper);text-shadow:0 1px 3px rgba(0,0,0,.4);white-space:nowrap}

/* services */
.services-band{left:0;top:345px;width:685px;height:289px;background:var(--mist)}
.services{left:74px;top:300px;width:537px;height:346px;background:var(--paper);border-top:3px solid var(--brand);box-shadow:0 2px 6px rgba(0,0,0,.06)}
.services h2{position:absolute;top:30px;width:100%;text-align:center;font-family:"Lora",Georgia,serif;font-weight:700;font-size:14px;letter-spacing:2px;color:var(--navy)}
.service{position:absolute;top:75px;width:147px;text-align:center}
.service-photo{height:107px;width:147px}
.service h3{margin-top:22px;height:26px;font-family:"Montserrat",Arial,sans-serif;font-weight:500;font-size:8.2px;line-height:11px;color:var(--ink)}
.service p{margin:10px auto 0;width:112px;font-size:6.4px;line-height:9px;color:var(--ink)}
.btn{display:inline-block;font-family:"Montserrat",Arial,sans-serif;font-weight:700;font-size:6.4px;color:var(--paper);background:var(--brand);padding:6px 9px;outline:1px solid var(--brand);outline-offset:2px;text-decoration:none}
.service .btn{margin-top:20px}
.divider{top:137px;width:1px;height:184px;background:var(--rule)}

/* about */
.about{left:0;top:634px;width:685px;height:319px;
  background:linear-gradient(180deg,#6f6aa8 0%,#9c86b8 35%,#d59fb6 60%,#e8b8a8 75%,#3b3a55 92%,#2a2a40 100%)}
.portrait{left:75px;top:680px;width:225px;height:273px;background:linear-gradient(180deg,#b89290 0%,#3a3a4a 45%,#1e2332 100%);border-radius:80px 80px 0 0}
.about-text{left:320px;top:683px;width:270px}
.about-kicker{font-family:"Lora",Georgia,serif;font-weight:600;font-size:12.5px;letter-spacing:1.5px;color:var(--navy)}
.about-name{margin-top:4px;font-family:"Lora",Georgia,serif;font-weight:600;font-size:17px;letter-spacing:.5px;color:var(--paper)}
.about-text p{margin-top:12px;font-size:7px;line-height:11px;color:#2a2a3a}
.about-text p+p{margin-top:10px}
.about-text .btn{margin-top:18px}

/* footer */
.footer{left:0;top:953px;width:685px;height:247px;background:var(--brand-dark)}
.pillar{left:24px;top:988px;width:50px;height:157px;background:rgba(255,255,255,.08)}
.footer .brand{left:92px;top:1036px;font-size:16px}
.footer .brand-square{width:30px;height:30px;background:var(--brand-dark);border:2px solid var(--paper)}
.contact{left:277px;top:999px;color:var(--paper);font-family:"Montserrat",Arial,sans-serif}
.contact h4{font-weight:700;font-size:7.5px}
.contact ul{list-style:none;margin-top:18px}
.contact li{display:flex;gap:8px;font-family:"Open Sans",Arial,sans-serif;font-size:6.4px;line-height:9px;margin-bottom:11px}
.contact svg{flex:none;margin-top:1px}
.map{left:408px;top:986px;width:202px;height:124px;background:linear-gradient(135deg,#eeeeec,#dcdfe3)}
.footer-rule{left:0;top:1144px;width:685px;height:1px;background:rgba(255,255,255,.12)}
.copyright{left:0;top:1170px;width:685px;text-align:center;font-size:6.4px;color:var(--paper)}
</style>
</head>
<body>

<section class="abs hero" role="img" aria-label="Harbour city skyline with arch bridge at sunset"></section>
<div class="abs brand"><span class="brand-square"></span>CASTELLAN LEGAL</div>
<nav class="abs nav">
  <a class="is-active" href="#">HOME</a><a href="#">ABOUT US</a><a href="#">SERVICES</a><a href="#">BLOG</a><a href="#">CONTACT US</a>
</nav>
<h1 class="abs tagline">WE GET RESULTS</h1>

<div class="abs services-band"></div>
<section class="abs services">
  <h2>OUR SERVICES</h2>
  <article class="service" style="left:21px">
    <div class="service-photo" role="img" aria-label="Business handshake" style="background:linear-gradient(135deg,#e4e6e8,#9ea4aa 60%,#3a3d44)"></div>
    <h3>Corporate Transactions<br>and Regulation</h3>
    <p>Sed ut perspiciatis unde omnis iste natus error sit voluptatem accu santium doloremque laud antium, totam rem aperiam, eaque ipsa quae ab illo .</p>
    <a class="btn" href="#">READ MORE</a>
  </article>
  <div class="abs divider" style="left:182px"></div>
  <article class="service" style="left:198px">
    <div class="service-photo" role="img" aria-label="Team meeting around a table" style="background:linear-gradient(180deg,#dfe6ea,#b7a89a 60%,#6c5e56)"></div>
    <h3>Business Law and<br>Dispute Resolution</h3>
    <p>Sed ut perspiciatis unde omnis iste natus error sit voluptatem accu santium doloremque laud antium, totam rem aperiam, eaque ipsa quae ab illo .</p>
    <a class="btn" href="#">READ MORE</a>
  </article>
  <div class="abs divider" style="left:358px"></div>
  <article class="service" style="left:380px">
    <div class="service-photo" role="img" aria-label="Traveller with luggage at an airport window" style="background:linear-gradient(135deg,#a8c4c8,#3d6a78 55%,#0f2a36)"></div>
    <h3>Migration<br>Assistance</h3>
    <p>Sed ut perspiciatis unde omnis iste natus error sit voluptatem accu santium doloremque laud antium, totam rem aperiam, eaque ipsa quae ab illo .</p>
    <a class="btn" href="#">READ MORE</a>
  </article>
</section>

<section class="abs about" role="img" aria-label="City skyline at dusk"></section>
<div class="abs portrait" role="img" aria-label="Portrait of Marcus Castellan in a suit"></div>
<div class="abs about-text">
  <div class="about-kicker">ABOUT</div>
  <div class="about-name">MARCUS CASTELLAN</div>
  <p>Marcus's rare regulatory experience in public fundraisings and mergers and acquisitions is a compelling advantage for any company seeking to complete a significant transaction quickly.</p>
  <p>Marcus assisted draft the Commission's regulatory guidance on prospectuses. With his team Marcus was awarded a National Service Medallion, "reserved for the highest level of recognition",</p>
  <a class="btn" href="#">READ MORE</a>
</div>

<footer class="abs footer"></footer>
<div class="abs pillar" role="img" aria-label="Faint classical column decoration"></div>
<div class="abs brand"><span class="brand-square"></span>CASTELLAN LEGAL</div>
<div class="abs contact">
  <h4>CONTACT US</h4>
  <ul>
    <li><svg width="6" height="8" viewBox="0 0 6 8"><path d="M3 0a3 3 0 0 1 3 3c0 2-3 5-3 5S0 5 0 3a3 3 0 0 1 3-3z" fill="#fff"/><circle cx="3" cy="3" r="1" fill="#0a3380"/></svg><span>88 Harbour Lane<br>Northgate, SA 5085</span></li>
    <li><svg width="7" height="7" viewBox="0 0 8 8"><path d="M1 0l2 2-1 1.2a5 5 0 0 0 2.8 2.8L6 5l2 2-1 1C3 8 0 5 0 1z" fill="#fff"/></svg><span>555.010.2040</span></li>
    <li><svg width="8" height="6" viewBox="0 0 8 6"><rect width="8" height="6" fill="#fff"/><path d="M0 0l4 3 4-3" stroke="#0a3380" fill="none" stroke-width=".8"/></svg><span>info@castellanlegal.com</span></li>
  </ul>
</div>
<div class="abs map" role="img" aria-label="Street map showing the office location"></div>
<div class="abs footer-rule"></div>
<div class="abs copyright">Copyrights @ 2018 All Rights Reserved</div>

</body>
</html>
```